Velk Partners Building Business Cards

We need a business card that reflects our business as "Solar Experts" in San Diego. Browse our website www.velkpartners.example our License needs to be displayed as "CSLB# 3867140" our phone number is (619) 555-0187

Save thousands on your electric bills and increase the value of your home while helping to protect the environment. Our solar installation experts will help you design the system that's right for you, using only the highest quality equipment that will look great and give you ideal performance. Our goal is to make you energy independent, and get your electric bill to 0.

Paul Osterby
(619) 555-0187
paul@velkpartners.example

Target Market(s)

Home owners in san diego looking for solar

Industry/Entity Type

Solar Energy

Contact Information for Business Card

Paul Osterby
(619) 555-0187
paul@velkpartners.example

Font styles to use
Other font styles liked:
• Use our logo font

Requirements
Must have
• License needs to be displayed as "CSLB# 3867140" our phone number is (619) 555-0187
Nice to have
• Real images of rooftop home solar in san diego
Should not have
• our business address

```html
<!DOCTYPE html>
<html lang="en">
<head>
<meta charset="utf-8">
<title>Velk Partners Building – Business Cards</title>
<link rel="stylesheet" href="https://fonts.googleapis.com/css2?family=Ubuntu:wght@700&family=Open+Sans:wght@400;700&display=swap">
<style>
  :root {
    --navy: #173a7e;
    --navy-deep: #12306b;
    --sun: #f5a916;
    --paper: #ffffff;
    --ink: #4a4f5a;
    --backdrop: #e6e4e0;
  }
  * { box-sizing: border-box; margin: 0; padding: 0; }
  html, body { width: 1200px; height: 950px; overflow: hidden; }
  body {
    background: var(--backdrop);
    font-family: "Open Sans", Arial, sans-serif;
    position: relative;
  }
  .card {
    position: absolute;
    left: 300px;
    width: 600px;
    height: 343px;
    border-radius: 4px;
    overflow: hidden;
    box-shadow: 0 10px 28px rgba(0,0,0,.22);
  }
  .card-front { top: 90px; background: var(--paper); }
  .card-back { top: 510px; background: var(--navy); }
  .front-art { position: absolute; inset: 0; }

  .brand {
    display: flex;
    align-items: center;
    gap: 10px;
    font-family: "Ubuntu", Arial, sans-serif;
    font-weight: 700;
  }
  .brand-dot { border-radius: 50%; background: var(--sun); flex: none; }

  .front-brand {
    position: absolute;
    left: 34px;
    top: 92px;
    width: 270px;
    color: var(--navy);
    font-size: 30px;
    line-height: 1.05;
  }
  .front-brand .brand-dot { width: 18px; height: 18px; }

  .contact {
    position: absolute;
    left: 38px;
    top: 206px;
    list-style: none;
    font-size: 13.5px;
    color: var(--ink);
    line-height: 1.75;
  }
  .contact li { display: flex; align-items: center; gap: 8px; }
  .contact .license { padding-left: 0; margin-bottom: 2px; }
  .contact svg { width: 12px; height: 12px; flex: none; fill: var(--navy); }

  .person {
    position: absolute;
    right: 30px;
    top: 138px;
    text-align: right;
  }
  .person-name {
    color: var(--sun);
    font-weight: 700;
    font-size: 20px;
    letter-spacing: .5px;
    text-transform: uppercase;
  }
  .person-role {
    color: var(--paper);
    font-size: 13px;
    margin-top: 4px;
    letter-spacing: .5px;
  }

  .back-brand {
    position: absolute;
    inset: 0;
    justify-content: center;
    color: var(--paper);
    font-size: 36px;
  }
  .back-brand .brand-dot { width: 22px; height: 22px; }
</style>
</head>
<body>

<section class="card card-front" aria-label="Card front">
  <svg class="front-art" viewBox="0 0 600 343" aria-hidden="true">
    <path d="M372 0 C 300 110, 440 220, 330 343" fill="none" stroke="var(--sun)" stroke-width="16"/>
    <path d="M386 0 C 314 110, 454 220, 344 343" fill="none" stroke="var(--navy)" stroke-width="3"/>
    <path d="M394 0 C 322 110, 462 220, 352 343 L600 343 L600 0 Z" fill="var(--navy)"/>
  </svg>

  <div class="brand front-brand">
    <span class="brand-name">Velk Partners Building</span>
    <span class="brand-dot"></span>
  </div>

  <ul class="contact">
    <li class="license">CSLB# 3867140</li>
    <li>
      <svg viewBox="0 0 24 24"><path d="M6.6 10.8a15.1 15.1 0 0 0 6.6 6.6l2.2-2.2c.3-.3.7-.4 1-.2 1.1.4 2.3.6 3.6.6.6 0 1 .4 1 1V20c0 .6-.4 1-1 1A17 17 0 0 1 3 4c0-.6.4-1 1-1h3.5c.6 0 1 .4 1 1 0 1.3.2 2.5.6 3.6.1.3 0 .7-.2 1z"/></svg>
      (619) 555-0187
    </li>
    <li>
      <svg viewBox="0 0 24 24"><path d="M2 5h20v14H2z M4 7v.5l8 5 8-5V7z" fill-rule="evenodd"/></svg>
      paul@velkpartners.example
    </li>
    <li>
      <svg viewBox="0 0 24 24"><circle cx="12" cy="12" r="10"/></svg>
      www.velkpartners.example
    </li>
  </ul>

  <div class="person">
    <p class="person-name">Paul Osterby</p>
    <p class="person-role">CEO/FOUNDER</p>
  </div>
</section>

<section class="card card-back" aria-label="Card back">
  <div class="brand back-brand">
    <span class="brand-name">Velk Partners Building</span>
    <span class="brand-dot"></span>
  </div>
</section>

</body>
</html>
```